New Business Card Design Project

We require a business card design for Vexalund, a newly established Indian company.
Our focus is on the development, manufacturing, and export of a diverse array of pharmaceutical products on a global scale. The card should convey a professional appearance, as our primary markets are in Africa, China, and Southeast Asian nations.
We envision a two-sided business card, with the reverse side dedicated to a logo set against a solid color or an elegantly designed pattern. The corners should be rounded. We would appreciate seeing both horizontal and vertical design options. We trust the designer to utilize their expertise in creating this design.

The content for the business card is included in the attached Word file.

Target Market(s)

Our primary markets are in Africa, China, and Southeast Asian, Latin America, Maldives, Sri Lanka

Industry/Entity Type

Pharmaceutical Manufacturing and Export

Contact Information for Business Card

Colors

Designer to choose colors to be used in the design.

Requirements
Must have
• The reverse side of the business card features solely the logo along with the tagline, "Care in Every Dose."
Should not have
• The logo should not exceed two instances, encompassing both the front and back sides of the card.

```html
<!DOCTYPE html>
<html lang="en">
<head>
<meta charset="utf-8">
<title>Vexalund Business Card</title>
<link rel="stylesheet" href="https://fonts.googleapis.com/css2?family=Montserrat:wght@800&family=Open+Sans:wght@400;700&family=Poppins:wght@400&display=swap">
<style>
  :root {
    --stage: #232323;
    --coral: #ef6350;
    --ink: #212125;
    --blue: #2fa6e0;
    --white: #ffffff;
  }
  * { box-sizing: border-box; margin: 0; padding: 0; }
  html, body { width: 1200px; height: 780px; overflow: hidden; }
  body { background: var(--stage); position: relative; font-family: "Open Sans", sans-serif; }

  .card {
    position: absolute;
    width: 600px;
    height: 343px;
    border-radius: 26px;
    overflow: hidden;
  }

  /* Reverse side */
  .card--back {
    left: 70px; top: 40px;
    background: var(--coral);
    display: flex; flex-direction: column; align-items: center; justify-content: center;
  }
  .brand-mark { display: flex; align-items: center; gap: 14px; }
  .brand-mark__dot { width: 22px; height: 22px; border-radius: 50%; background: var(--white); }
  .brand-mark__name {
    font-family: "Montserrat", sans-serif; font-weight: 800;
    font-size: 64px; line-height: 1; letter-spacing: 1px; color: var(--white);
  }
  .tagline {
    margin-top: 18px;
    font-family: "Poppins", sans-serif; font-size: 15px; letter-spacing: 1.5px;
    color: var(--white);
  }

  /* Front side */
  .card--front {
    left: 530px; top: 400px;
    background: var(--ink);
  }
  .holder { position: absolute; left: 0; top: 40px; padding-left: 26px; }
  .holder__bar { position: absolute; left: 0; top: 6px; width: 12px; height: 58px; background: var(--blue); }
  .holder__name { font-size: 27px; line-height: 1.15; white-space: nowrap; }
  .holder__first { color: var(--blue); font-weight: 700; }
  .holder__last { color: var(--coral); font-weight: 400; }
  .holder__role { color: var(--white); font-size: 15px; }

  .front-brand {
    position: absolute; right: 34px; top: 70px;
    font-family: "Montserrat", sans-serif; font-weight: 800;
    font-size: 42px; line-height: 1; color: var(--blue);
  }

  .contacts { position: absolute; right: 30px; top: 150px; list-style: none; }
  .contacts__item {
    display: flex; align-items: center; justify-content: flex-end; gap: 10px;
    color: var(--white); font-size: 14px; line-height: 26px; white-space: nowrap;
  }
  .contacts__icon { width: 16px; height: 16px; flex: none; }

  .address {
    position: absolute; left: 38px; bottom: 34px;
    color: var(--white); font-size: 14px; line-height: 1.5; font-style: normal;
  }
</style>
</head>
<body>

<section class="card card--back" aria-label="Card reverse">
  <div class="brand-mark">
    <span class="brand-mark__dot"></span>
    <span class="brand-mark__name">Vexalund</span>
  </div>
  <p class="tagline">Care in Every Dose.</p>
</section>

<section class="card card--front" aria-label="Card front">
  <div class="holder">
    <span class="holder__bar"></span>
    <p class="holder__name"><span class="holder__first">Arjun</span> <span class="holder__last">K. Velankar</span></p>
    <p class="holder__role">CEO</p>
  </div>

  <div class="front-brand">Vexalund</div>

  <ul class="contacts">
    <li class="contacts__item">+919 555018274
      <svg class="contacts__icon" viewBox="0 0 16 16" aria-hidden="true"><rect x="4" y="1" width="8" height="14" rx="1.5" fill="none" stroke="#ef6350" stroke-width="1.5"/></svg>
    </li>
    <li class="contacts__item">www.vexalund.com
      <svg class="contacts__icon" viewBox="0 0 16 16" aria-hidden="true"><circle cx="8" cy="8" r="6.5" fill="none" stroke="#2fa6e0" stroke-width="1.5"/><ellipse cx="8" cy="8" rx="3" ry="6.5" fill="none" stroke="#2fa6e0" stroke-width="1.2"/><line x1="1.5" y1="8" x2="14.5" y2="8" stroke="#2fa6e0" stroke-width="1.2"/></svg>
    </li>
    <li class="contacts__item">avelankar@vexalund.com
      <svg class="contacts__icon" viewBox="0 0 16 16" aria-hidden="true"><rect x="1" y="3.5" width="14" height="10" rx="1" fill="#ef6350"/><path d="M1.5 4.5 L8 9.5 L14.5 4.5" fill="none" stroke="#212125" stroke-width="1.2"/></svg>
    </li>
  </ul>

  <address class="address">14, Sundar Nagar,<br>Nandpur, 440018, India</address>
</section>

</body>
</html>
```